Business card for Luxury Portable Restroom Trailer company

We are a Luxury Portable Restroom Trailer Company Called FALCRIDGE HIRES. Based in Orange County California. We provide portable restroom trailers for events, such as, Weddings, Concerts, Charity events, Sporting events, Tournaments, Corporate events, ect. We rent and Sell the Luxury restrooms. Our colors are white, grey, and Orange. As you will see in the logo we uploaded.
There are 2 people in the company so the names and titles will change for the 3 people but card will remain the same. Here is the information for each Person: Dwight Penner CFO 555 318-0476
next Person: Leon Marchetti VP 555 318-0476
Next Person: Owen Marchetti CEO 555 318-0476
Information to include on the card: Luxury Restroom Trailers Rental and Sales. Weddings, Concerts, Charity, Sporting and Corp. Events.

```html
<!DOCTYPE html>
<html lang="en">
<head>
<meta charset="utf-8">
<title>Falcridge Hires – Business Card</title>
<link rel="stylesheet" href="https://fonts.googleapis.com/css2?family=Michroma&family=Open+Sans:wght@400;600&display=swap">
<style>
  :root {
    --bg: #c9c9cb;
    --card-white: #ffffff;
    --card-dark: #4e4e50;
    --orange: #f26522;
    --grey: #5a5a5c;
    --white: #ffffff;
  }
  * { margin: 0; padding: 0; box-sizing: border-box; }
  html, body { width: 1200px; height: 876px; overflow: hidden; }
  body {
    background: var(--bg);
    position: relative;
    font-family: "Open Sans", Arial, sans-serif;
  }
  .card {
    position: absolute;
    width: 540px;
    height: 309px;
    border-radius: 4px;
    box-shadow: 0 10px 24px rgba(0,0,0,0.25);
  }
  .card--front { left: 50px; top: 420px; background: var(--card-white); }
  .card--back { left: 610px; top: 130px; background: var(--card-dark); }

  .brand {
    display: flex;
    align-items: center;
    gap: 10px;
    font-family: "Michroma", sans-serif;
    letter-spacing: 1px;
  }
  .brand__mark { width: 14px; height: 14px; background: var(--orange); flex: none; }
  .brand--front { position: absolute; left: 34px; top: 34px; font-size: 17px; color: var(--grey); }
  .brand--back {
    position: absolute; left: 0; right: 0; top: 0; bottom: 0;
    justify-content: center; font-size: 26px; color: var(--white);
  }
  .brand--back .brand__mark { width: 20px; height: 20px; }

  .person { position: absolute; left: 290px; top: 112px; font-family: "Michroma", sans-serif; }
  .person__name { font-size: 17px; letter-spacing: 1px; color: var(--grey); }
  .person__name .first { color: var(--orange); }
  .person__title { margin-top: 8px; font-size: 12px; color: var(--grey); }
  .person__phone {
    margin-top: 10px; display: flex; align-items: center; gap: 8px;
    font-size: 13px; color: var(--grey); letter-spacing: 1px;
  }
  .person__phone svg { width: 14px; height: 14px; }

  .services { position: absolute; left: 34px; bottom: 34px; }
  .services__headline {
    font-family: "Michroma", sans-serif; font-size: 11px;
    color: var(--orange); letter-spacing: 0.5px;
  }
  .services__events { margin-top: 8px; font-size: 13px; color: var(--grey); }
</style>
</head>
<body>
  <section class="card card--back" aria-label="Card back">
    <div class="brand brand--back"><span class="brand__mark"></span>FALCRIDGE HIRES</div>
  </section>

  <section class="card card--front" aria-label="Card front">
    <div class="brand brand--front"><span class="brand__mark"></span>FALCRIDGE HIRES</div>

    <div class="person">
      <div class="person__name"><span class="first">LEON</span> MARCHETTI</div>
      <div class="person__title">CFO</div>
      <div class="person__phone">
        <svg viewBox="0 0 24 24" aria-hidden="true"><path fill="#f26522" d="M6.6 10.8a15.1 15.1 0 0 0 6.6 6.6l2.2-2.2a1 1 0 0 1 1-.25 11.4 11.4 0 0 0 3.6.57 1 1 0 0 1 1 1V20a1 1 0 0 1-1 1A17 17 0 0 1 3 4a1 1 0 0 1 1-1h3.5a1 1 0 0 1 1 1c0 1.25.2 2.45.57 3.6a1 1 0 0 1-.25 1z"/></svg>
        555.204.7713
      </div>
    </div>

    <div class="services">
      <div class="services__headline">LUXURY RESTROOM TRAILERS RENTAL AND SALES</div>
      <div class="services__events">Weddings | Concerts | Charity | Sporting | Corp. Events</div>
    </div>
  </section>
</body>
</html>
```